Purple Heart Veteran Owned Telecommunications Company

I need to develop my current website (brightwirel.com) into something more upbeat and modern. I created the existing one with SiteKindle and it's very basic. I'm open to using any type of website builder and not just SiteKindle. I feel like SiteKindle is pretty basic. I want something customized to me and my company. I plan on doing a Zorbix Ad, Email Marketing, and Mail Marketing campaign and SEO push. I want a website built so they can look up my company. We are a low voltage telecommunications company based out of Chicago. We are a General Contractor and I have technicians all throughout the US and Canada. I mainly appeal to the government and fortune 500 companies across the country. I focus on commercial and federal work with minor work in Residential. I need to appeal to everyone and not just locally. My company name is Brightwirel. I'm a Marine Corps veteran and my I created the company with my son in mind. We are a service disabled veteran owned small business. I'm open to any play on my logo or color scheme. I do like the color blue but I'm open to anything again. I would like a website that has little maintenance needed and something that is modern and sticks out with my competitors. I'm only in business for 2 years but I need to stick out to my competition so I can start building revenue through ads and getting my name out there with limited funds. I did have a logo and name created which I'm attaching. I'm completely open to changing it if someone can come up with something creative. I would like someone that understands SEO and can help feed work to my site. I'm also open to paying more for the right website that gets everything I want. I know I need to add more pages and more professional. Please use my website as a template but also feel free to come up with any new ideas. I would like some feedback or ideas on what else to add to my website or remove so I can appeal to my audience and look more authentic.

Target Market(s)

Commercial Companies locally in Chicago, and Fortune 500 companies and the government

Industry/Entity Type

Telecommunications

Coding

Number of Pages Required

Font styles to use
Sans Serif

Requirements
Must have
• A Modern, fresh look that is customized and original. Something that sticks out to my customers.
Nice to have
• Anything that sticks out and isn't stock. I'm open to anything that is unique and different.
Should not have
• Nothing Generic. I would like something custom tailored to my business

```html
<!DOCTYPE html>
<html lang="en">
<head>
<meta charset="utf-8">
<title>Brightwirel – General Contractor</title>
<link href="https://fonts.googleapis.com/css2?family=Roboto:wght@300;400;500;700&family=Arimo:wght@400&display=swap" rel="stylesheet">
<style>
:root{
  --navy:#0c1d5c;
  --navy-deep:#081546;
  --navy-mid:#1b2f7c;
  --ink:#222;
  --body:#4a4a4a;
  --muted:#777;
  --line:#e2e2e2;
  --panel:#f1f1f1;
  --footer:#222222;
  --white:#fff;
}
*{margin:0;padding:0;box-sizing:border-box}
html,body{width:1200px;height:3478px;overflow:hidden}
body{font-family:"Roboto",sans-serif;color:var(--ink);background:var(--white);position:relative}
section,header,footer{position:relative;width:1200px}
.abs{position:absolute}

/* header */
.site-header{height:142px;border-top:4px solid var(--navy)}
.brand{left:112px;top:62px;font-size:31px;font-weight:500;letter-spacing:3px;color:var(--navy);display:flex;align-items:center;gap:10px}
.brand-mark{width:16px;height:16px;background:var(--navy)}
.contact-chip{top:24px;display:flex;align-items:center;gap:12px}
.chip-icon{width:42px;height:42px;border:1.5px solid var(--navy);border-radius:50%;display:flex;align-items:center;justify-content:center}
.chip-label{font-size:13px;color:var(--muted)}
.chip-value{font-size:17px;color:var(--ink);margin-top:3px}
.main-nav{top:98px;font-size:14px;font-weight:500;color:var(--ink)}
.main-nav span{position:absolute;white-space:nowrap}
.main-nav .active{color:var(--navy)}

/* hero */
.hero{height:713px}
.hero-bg{inset:0;background:radial-gradient(ellipse 70% 45% at 50% 100%,#3fb0a4 0%,#1f5ea8 30%,transparent 70%),radial-gradient(ellipse at 75% 45%,#2b4fc4 0%,#15298a 40%,#0a123f 80%),#0a123f}
.hero-title{left:0;right:0;top:262px;text-align:center;color:var(--white);font-size:92px;font-weight:500;letter-spacing:1px}
.hero-sub{left:0;right:0;top:374px;text-align:center;color:var(--white);font-size:41px;font-weight:300;letter-spacing:1px}
.btn-ghost{left:510px;top:444px;width:179px;height:57px;border:2px solid var(--white);border-radius:30px;color:var(--white);font-size:17px;font-weight:500;display:flex;align-items:center;justify-content:center}

/* services */
.service-card{top:776px;width:307px;height:338px;background:var(--white);border:1px solid var(--line);border-radius:8px;box-shadow:0 2px 8px rgba(0,0,0,.06)}
.service-card svg{position:absolute;left:30px;top:34px}
.service-card h3{position:absolute;left:32px;top:124px;font-size:18px;font-weight:500;color:var(--ink)}
.service-card p{position:absolute;left:32px;top:159px;width:252px;font-family:"Arimo",sans-serif;font-size:13.5px;line-height:24.5px;color:var(--body)}
.btn-outline{position:absolute;left:32px;top:256px;width:137px;height:49px;border:2px solid var(--navy);border-radius:26px;color:var(--navy);font-size:15px;font-weight:500;display:flex;align-items:center;justify-content:center}

/* welcome */
.welcome-title{left:112px;top:1226px;font-size:30px;font-weight:500;color:var(--ink)}
.welcome-title b{font-weight:500;color:var(--navy)}
.rule{height:3px;width:54px;background:#333}
.welcome-copy{left:112px;top:1302px;width:500px;font-family:"Arimo",sans-serif;font-size:15px;line-height:29.2px;color:var(--body)}
.btn-solid{left:112px;top:1569px;width:162px;height:59px;background:var(--navy);border-radius:30px;color:var(--white);font-size:16px;font-weight:500;display:flex;align-items:center;justify-content:center}
.welcome-photo{left:620px;top:1212px;width:467px;height:404px;background:linear-gradient(135deg,#1d2d6e 0%,#3a3f55 45%,#5a5040 70%,#1b2b6a 100%);border-radius:4px}

/* markets */
.markets{position:absolute;top:1690px;height:569px;background:linear-gradient(180deg,var(--navy-deep) 0%,var(--navy) 55%,var(--navy-mid) 100%)}
.markets h2{position:absolute;left:0;right:0;top:60px;text-align:center;color:var(--white);font-size:34px;font-weight:500}
.markets .rule{position:absolute;left:573px;top:117px;background:var(--white)}
.market{position:absolute;top:159px;width:312px;text-align:center;color:var(--white)}
.market-photo{height:234px}
.market h3{margin-top:22px;font-size:22px;font-weight:400}
.market p{margin-top:10px;font-family:"Arimo",sans-serif;font-size:15.5px;line-height:25px;color:#c9cfe6}

/* events */
.events{position:absolute;top:2259px;height:611px}
.events-photo{left:112px;top:78px;width:520px;height:448px;background:linear-gradient(160deg,#9fb6d4 0%,#2f6fd0 35%,#1750b4 65%,#2a3f6e 100%)}
.events-frame{left:539px;top:94px;width:549px;height:416px;border:1px solid var(--navy)}
.events-card{left:556px;top:102px;width:524px;height:398px;background:var(--white);box-shadow:0 2px 12px rgba(0,0,0,.12)}
.events-card h2{position:absolute;left:31px;top:62px;font-size:30px;font-weight:400;color:#2a2a2a}
.event-meta{position:absolute;left:34px;top:118px;display:flex;gap:32px;font-size:15px;color:var(--navy)}
.event-meta span{display:flex;align-items:center;gap:9px}
.event-lead{position:absolute;left:34px;top:160px;width:460px;font-size:16px;line-height:27px;color:var(--ink)}
.event-body{position:absolute;left:34px;top:230px;width:462px;font-family:"Arimo",sans-serif;font-size:13.3px;line-height:26px;color:var(--muted)}

/* partners */
.partners{position:absolute;top:2870px;height:222px;background:var(--panel)}
.partner{position:absolute;top:62px;width:170px;height:99px;background:var(--white);border:1px solid #ddd;display:flex;align-items:center;justify-content:center;font-size:22px;color:#b3b3b3}

/* footer */
.site-footer{position:absolute;top:3092px;height:386px;background:var(--footer);color:var(--white)}
.site-footer h4{position:absolute;top:46px;font-size:21px;font-weight:500;letter-spacing:.5px}
.field{position:absolute;height:35px;background:var(--white);font-size:12px;color:#333;padding:10px 12px}
.btn-submit{position:absolute;left:116px;top:240px;width:97px;height:34px;background:#555;font-size:13px;display:flex;align-items:center;justify-content:center}
.addr-item{position:absolute;left:593px;display:flex;gap:16px;font-size:12.5px;line-height:20px}
.addr-icon{width:41px;height:41px;border:1.5px solid var(--white);border-radius:50%;display:flex;align-items:center;justify-content:center;flex:none}
.footer-brand{position:absolute;left:844px;top:160px;width:240px;text-align:center;font-size:29px;font-weight:500;letter-spacing:3px}
.social{position:absolute;top:215px;width:34px;height:34px;border:1.5px solid var(--white);border-radius:50%}
.footer-rule{position:absolute;left:112px;right:112px;top:313px;height:1px;background:#3a3a3a}
.copyright{position:absolute;left:0;right:0;top:342px;text-align:center;font-size:15px}
</style>
</head>
<body>

<header class="site-header">
  <div class="abs brand"><span class="brand-mark"></span>BRIGHTWIREL</div>
  <div class="abs contact-chip" style="left:616px">
    <div class="chip-icon"><svg width="18" height="18" viewBox="0 0 24 24" fill="none" stroke="#0c1d5c" stroke-width="2"><path d="M22 16.9v3a2 2 0 0 1-2.2 2 19.8 19.8 0 0 1-8.6-3.1 19.5 19.5 0 0 1-6-6A19.8 19.8 0 0 1 2.1 4.2 2 2 0 0 1 4.1 2h3a2 2 0 0 1 2 1.7c.1.9.4 1.8.7 2.7a2 2 0 0 1-.5 2.1L8 9.8a16 16 0 0 0 6 6l1.3-1.3a2 2 0 0 1 2.1-.4c.9.3 1.8.6 2.7.7a2 2 0 0 1 1.7 2z"/></svg></div>
    <div><div class="chip-label">Call Us</div><div class="chip-value">312-555-0148</div></div>
  </div>
  <div class="abs contact-chip" style="left:833px">
    <div class="chip-icon"><svg width="18" height="18" viewBox="0 0 24 24" fill="none" stroke="#0c1d5c" stroke-width="2"><rect x="2" y="5" width="20" height="14" rx="1"/><path d="M2 6l10 7 10-7"/></svg></div>
    <div><div class="chip-label">Email</div><div class="chip-value">Support@brightwirel.com</div></div>
  </div>
  <nav class="abs main-nav" style="left:0;width:1200px">
    <span class="active" style="left:533px">HOME</span>
    <span style="left:621px">LOW VOLTAGE</span>
    <span style="left:767px">MARKETS</span>
    <span style="left:880px">OUR TEAM</span>
    <span style="left:999px">CONTACT US</span>
  </nav>
</header>

<section class="hero">
  <div class="abs hero-bg" role="img" aria-label="Night view of the earth from space with glowing network arcs"></div>
  <h1 class="abs hero-title">BRIGHTWIREL</h1>
  <div class="abs hero-sub">GENERAL CONTRACTOR</div>
  <div class="abs btn-ghost">READ MORE</div>
</section>

<article class="abs service-card" style="left:112px">
  <svg width="70" height="72" viewBox="0 0 70 72" fill="none" stroke="#0c1d5c" stroke-width="2.5"><rect x="4" y="14" width="34" height="22" rx="3"/><path d="M12 4v10M30 4v10M10 36c0 12 6 18 11 18s11-6 11-18M21 54v14M48 70V22a8 8 0 0 1 16 0v30"/></svg>
  <h3>STRUCTURED CABLING</h3>
  <p>Our company has a network &nbsp;contractors nationally and in Canada. &nbsp;We also have the ability to provide our own</p>
  <div class="btn-outline">READ MORE</div>
</article>
<article class="abs service-card" style="left:447px">
  <svg width="80" height="72" viewBox="0 0 80 72" fill="none" stroke="#0c1d5c" stroke-width="2.5"><rect x="3" y="16" width="74" height="46" rx="2"/><path d="M30 70h20M40 62v8"/><circle cx="40" cy="12" r="8"/><circle cx="40" cy="12" r="3"/><path d="M14 40h52M26 34v12M54 34v12"/></svg>
  <h3>INSTALLATION</h3>
  <p>Our company has a network &nbsp;contractors nationally and in Canada. &nbsp;We also have the ability to provide our own</p>
  <div class="btn-outline">READ MORE</div>
</article>
<article class="abs service-card" style="left:782px">
  <svg width="76" height="74" viewBox="0 0 76 74" fill="none" stroke="#0c1d5c" stroke-width="2.5"><circle cx="12" cy="12" r="8"/><circle cx="62" cy="12" r="9"/><circle cx="38" cy="38" r="10"/><circle cx="14" cy="60" r="9"/><circle cx="62" cy="60" r="8"/><path d="M18 18l12 12M55 19l-9 11M30 45l-9 8M46 45l10 9"/></svg>
  <h3>NETWORKING</h3>
  <p>Our company has a network &nbsp;contractors nationally and in Canada. &nbsp;We also have the ability to provide our own</p>
  <div class="btn-outline">READ MORE</div>
</article>

<h2 class="abs welcome-title">WELCOME TO <b>BRIGHTWIREL</b></h2>
<div class="abs rule" style="left:112px;top:1280px"></div>
<p class="abs welcome-copy">Our company has a network of subcontractors nationally and in Canada. We also have the ability to provide our own labor which allows us to offer a competitive edge and provide immediate assistance to our customers. Our past projects include both new construction and repairs/restorations. Occupied and fully operational job sites are never a problem. And we can also plan, manage, &amp; design jobs.We offer an end-to-end experience that includes seamless communication, budgeting, staffing organization, and solid, quality handiwork every time.</p>
<div class="abs btn-solid">READ MORE</div>
<div class="abs welcome-photo" role="img" aria-label="Photo of a service member in uniform"></div>

<section class="markets">
  <h2>OUR MARKETS</h2>
  <div class="rule"></div>
  <div class="market" style="left:112px">
    <div class="market-photo" role="img" aria-label="Photo of modern residential apartment buildings" style="background:linear-gradient(180deg,#dfe6ee 0%,#b7c3cf 40%,#8a5a44 70%,#5f6b55 100%)"></div>
    <h3>RESIDENTIAL</h3>
    <p>Let us assist you with your project!<br>No project is to big or small.</p>
  </div>
  <div class="market" style="left:445px">
    <div class="market-photo" role="img" aria-label="Photo of a commercial office corridor" style="background:linear-gradient(100deg,#5a2a18 0%,#8a4322 35%,#9fb3c4 65%,#4d6070 100%)"></div>
    <h3>COMMERCIAL</h3>
    <p>Brightwirel is a leading services provider<br>for Fortune 500 businesses</p>
  </div>
  <div class="market" style="left:777px">
    <div class="market-photo" role="img" aria-label="Photo of a domed government capitol building" style="background:linear-gradient(180deg,#2f57b8 0%,#6a8fd6 40%,#d9dde3 65%,#6c6f75 100%)"></div>
    <h3>FEDERAL</h3>
    <p>We are a trusted provider for the U.S.<br>Government with proven</p>
  </div>
</section>

<section class="events">
  <div class="abs events-photo" role="img" aria-label="Photo of blue network cables plugged into a patch panel"></div>
  <div class="abs events-frame"></div>
  <div class="abs events-card">
    <h2>LATEST EVENTS</h2>
    <div class="event-meta">
      <span><svg width="14" height="14" viewBox="0 0 24 24" fill="none" stroke="#0c1d5c" stroke-width="2.5"><rect x="3" y="5" width="18" height="16" rx="1"/><path d="M3 10h18M8 2v5M16 2v5"/></svg>Wednesday 14Th April 2021</span>
      <span><svg width="14" height="14" viewBox="0 0 24 24" fill="none" stroke="#0c1d5c" stroke-width="2.5"><circle cx="12" cy="12" r="9"/><path d="M12 7v5l3 2"/></svg>6:30Pm To 8:30</span>
    </div>
    <p class="event-lead">Our Mission is to work hard every day to make Brightwirel the world's most respected company brand.</p>
    <p class="event-body">Sed ut perspiciatis unde omnis iste natus error sit voluptatem accusantium doloremque laudantium, totam rem aperiam, eaque ipsa quae ab illo invent ore veritatis et quasi architecto beatae vitae dicta sunt explicabo. Nemo enim ipsam voluptatem quia voluptas sit aspernatur aut odit aut fugit, sed dolores eos qui ratione voluptatem sequi nesciunt.</p>
  </div>
</section>

<section class="partners">
  <div class="partner" style="left:112px">Kelvara</div>
  <div class="partner" style="left:313px">Ondry</div>
  <div class="partner" style="left:516px">Plinthory</div>
  <div class="partner" style="left:717px;font-size:18px">Farreach Grid</div>
  <div class="partner" style="left:918px">Nordvane</div>
</section>

<footer class="site-footer">
  <h4 style="left:117px">CONTACT US</h4>
  <div class="field" style="left:117px;top:98px;width:180px">First Name :</div>
  <div class="field" style="left:306px;top:98px;width:181px">Last Name :</div>
  <div class="field" style="left:117px;top:141px;width:180px">Company Name :</div>
  <div class="field" style="left:306px;top:141px;width:181px">Email address :</div>
  <div class="field" style="left:117px;top:187px;width:370px">Comment :</div>
  <div class="btn-submit">SUBMIT</div>

  <h4 style="left:601px">ADDRESS</h4>
  <div class="addr-item" style="top:93px">
    <div class="addr-icon"><svg width="14" height="16" viewBox="0 0 24 24" fill="#fff"><path d="M12 2a7 7 0 0 0-7 7c0 5 7 13 7 13s7-8 7-13a7 7 0 0 0-7-7zm0 9.5A2.5 2.5 0 1 1 12 6.5a2.5 2.5 0 0 1 0 5z"/></svg></div>
    <div>ADDRESS<br>Suite 5, 2 Lorem Ipsum<br>Lorem ipsum WA 6163</div>
  </div>
  <div class="addr-item" style="top:172px">
    <div class="addr-icon"><svg width="15" height="15" viewBox="0 0 24 24" fill="none" stroke="#fff" stroke-width="2"><path d="M22 16.9v3a2 2 0 0 1-2.2 2 19.8 19.8 0 0 1-8.6-3.1 19.5 19.5 0 0 1-6-6A19.8 19.8 0 0 1 2.1 4.2 2 2 0 0 1 4.1 2h3a2 2 0 0 1 2 1.7c.1.9.4 1.8.7 2.7a2 2 0 0 1-.5 2.1L8 9.8a16 16 0 0 0 6 6l1.3-1.3a2 2 0 0 1 2.1-.4c.9.3 1.8.6 2.7.7a2 2 0 0 1 1.7 2z"/></svg></div>
    <div>PHONE NUMBER<br>312-555-0148</div>
  </div>
  <div class="addr-item" style="top:238px">
    <div class="addr-icon"><svg width="15" height="13" viewBox="0 0 24 20" fill="#fff"><path d="M2 2h20v16H2z"/><path d="M2 3l10 7 10-7" stroke="#222" stroke-width="2" fill="none"/></svg></div>
    <div>EMAIL US<br>Support@brightwirel.com</div>
  </div>

  <div class="footer-brand">BRIGHTWIREL</div>
  <div class="social" style="left:902px"></div>
  <div class="social" style="left:945px"></div>
  <div class="social" style="left:989px"></div>

  <div class="footer-rule"></div>
  <div class="copyright">Copyright © 2021 Brightwirel - All Rights Reserved.</div>
</footer>

</body>
</html>
```